Harborview Estates Business Card for Apartment Buildings

Create business cards for resident managers who run apartment buildings. The audience is the public who are searching for apartment rentals, and current residents who live at the apartment building. Key design element will be incorporating the company logo, however, the logo cannot dominate. The building name and manager name are more important than the logo. Current business card design leaves little room for copy, so we may need to reduce the size on the current card to allow for more space for copy.

Target Market(s)

Adults 18-65 years of age, who are looking for an apartment rental, plus current residents who live at our apartment buildings.

Industry/Entity Type

Property Management

Contact Information for Business Card

A major design element will be use of the company logo. Important property and manager contact information must be part of the design. The size of the logo will need to be reduced to make room for building and manager contact copy.

Font styles to use
Sans Serif

Colors
3176b5
000000
959595
ffffff

Requirements
Must have
• 1) Incorporate the company logo.
• 2) Use the company colors (dark blue, black/grey, over white).
• 3) FEATURE THE BUILDING NAME
• 4) FEATURE THE MANAGER NAME
• 5) The company name is less important than BUILDING and MANAGER
• 6) Manager contact information
• **SEE ATTACHED CREATIVE BRIEF**
Nice to have
• 1) Back of card logo watermark
• 2) Ability to write notes on back of carfd
Should not have
• Avoid letting the company logo dominate the card, the building name and manager are more important than the company logo.

```html
<!DOCTYPE html>
<html lang="en">
<head>
<meta charset="utf-8">
<title>Harborview Estates – Resident Manager Business Card</title>
<link href="https://fonts.googleapis.com/css2?family=Roboto:wght@400;500;700&display=swap" rel="stylesheet">
<style>
  :root{
    --stage:#e6e7e9;
    --card:#ffffff;
    --card-edge:#cfd0d2;
    --brand-blue:#136daa;
    --ink:#2b2b2b;
    --ink-soft:#3a3a3a;
    --band-dark:#48484a;
  }
  *{box-sizing:border-box;margin:0;padding:0}
  html,body{width:1200px;height:1200px;overflow:hidden}
  body{background:var(--stage);font-family:"Roboto",Arial,sans-serif;position:relative;border:1px solid #8a8a8a}
  .card{position:absolute;left:257px;width:686px;height:392px;background:var(--card);border:1px solid var(--card-edge);overflow:hidden}
  .card--front{top:183px}
  .card--back{top:645px}

  .brand{position:absolute;display:flex;align-items:center;gap:8px;color:var(--brand-blue);font-weight:700;white-space:nowrap}
  .brand__dot{width:14px;height:14px;border-radius:50%;background:var(--brand-blue);flex:none}
  .card--front .brand{left:58px;top:178px;font-size:27px}
  .card--back .brand{right:44px;top:305px;font-size:23px}

  .manager{position:absolute;left:391px;top:73px}
  .manager__name{color:var(--brand-blue);font-size:28px;font-weight:500;line-height:1;letter-spacing:-.2px}
  .manager__title{color:var(--ink-soft);font-size:13px;margin-top:5px}

  .property{position:absolute;left:391px;top:143px}
  .property__name{color:var(--brand-blue);font-size:18.5px;font-weight:500;line-height:1.1}
  .property__address{color:var(--ink);font-size:15px;line-height:19px;margin-top:2px}

  .contacts{position:absolute;left:391px;top:224px;list-style:none}
  .contacts li{display:flex;align-items:center;gap:8px;color:var(--ink);font-size:15px;line-height:18.5px}
  .contacts svg{width:14px;height:14px;fill:var(--brand-blue);flex:none}

  .band{position:absolute;left:0;bottom:0;width:100%;height:28px}
  .band__dark{position:absolute;left:0;top:0;width:414px;height:100%;background:var(--band-dark)}
  .band__dot{position:absolute;left:414px;top:-10px;width:38px;height:38px;border-radius:50%;background:var(--card);border:3px solid var(--brand-blue)}
  .band__blue{position:absolute;left:452px;top:0;right:0;height:100%;background:var(--brand-blue);color:#fff;font-size:14px;display:flex;align-items:center;padding-left:26px;letter-spacing:.2px}

  .back-web{position:absolute;right:44px;top:343px;color:var(--ink-soft);font-size:16px;letter-spacing:.5px}
  .back-web b{color:var(--brand-blue);font-weight:500}
</style>
</head>
<body>
  <section class="card card--front">
    <div class="brand"><span class="brand__dot"></span>Harborview Estates</div>

    <div class="manager">
      <h1 class="manager__name">Marisol Delgado</h1>
      <p class="manager__title">Resident Manager</p>
    </div>

    <div class="property">
      <h2 class="property__name">Bayside Court Apartments</h2>
      <p class="property__address">2145 Willow Crest Street<br>Lakeview, CA 90210</p>
    </div>

    <ul class="contacts">
      <li><svg viewBox="0 0 16 16"><path d="M1 6c0-3 3-4 7-4s7 1 7 4l-3 1-1-2H5L4 7 1 6zm3 2h8l2 6H2l2-6zm4 1.5a2 2 0 100 4 2 2 0 000-4z"/></svg>555-210-4487</li>
      <li><svg viewBox="0 0 16 16"><path d="M4 1h8v14H4V1zm1.5 1.5v9h5v-9h-5zM8 12.5a.8.8 0 100 1.6.8.8 0 000-1.6z"/></svg>555-318-6620</li>
      <li><svg viewBox="0 0 16 16"><path d="M5 1h5l2 2v3H5V1zM2 7h12v7H2V7zm2 5h8v-2H4v2z"/></svg>555-402-7731</li>
      <li><svg viewBox="0 0 16 16"><path d="M1 3h14v10H1V3zm1.5 1.5L8 9l5.5-4.5v-.1h-11z"/></svg>marisol@harborviewest.com</li>
    </ul>

    <div class="band">
      <div class="band__dark"></div>
      <div class="band__blue">www.harborviewest.com</div>
      <div class="band__dot"></div>
    </div>
  </section>

  <section class="card card--back">
    <div class="brand"><span class="brand__dot"></span>Harborview Estates</div>
    <p class="back-web">www.<b>harborviewest</b>.com</p>
  </section>
</body>
</html>
```